Media Services Start-up -- Corporate Website and Logo Design. Inspiration required!

We need a logo design and corporate website design, including coding, for our start-up business.
Vennatra’s value proposition is based on bringing together media content from a vast number of geographies globally, adding human and AI curation, translation and editing, and delivering the content using tailored customer interfaces. On the one hand, the business brings together media coverage from all over the world, and on the other it brings together content, human skills and technology to deliver a supreme customer experience.
Vennatra is a B2B media monitoring and analytics business with emphasis on global customers. Vennatra's service offering is centred around sourcing media content from different markets, processing, storing and delivering the content and insights derived from it using an online platform / mobile app.
The messaging we want to create through the logo is:
- Global scope
- Speed of delivery
- Cost-efficiency
- Multi-lingual
- Tailor-made
- Trustworthy
Target Market(s)
Business to business, PR / Communications, Media, Marketing
Logo Text
Vennatra
Coding
Coded - Design and coding required
Number of Pages Required
5+ page
Font styles to use
Other font styles liked:
- See Design Brief for details
Colors
Designer to choose colors to be used in the design.

```html
<!DOCTYPE html>
<html lang="en">
<head>
<meta charset="utf-8">
<title>Vennatra – Global Media Intelligence</title>
<link href="https://fonts.googleapis.com/css2?family=Roboto:wght@400;500;700;900&display=swap" rel="stylesheet">
<style>
:root{
  --orange:#ff7a00;
  --ink:#333333;
  --text:#444444;
  --logo:#555555;
  --white:#ffffff;
  --footer:#333333;
  --footer-text:#e6e6e6;
  --line:#d6d6d6;
}
*{box-sizing:border-box;margin:0;padding:0}
html,body{width:1200px;height:3062px;overflow:hidden}
body{position:relative;background:var(--orange);font-family:"Roboto",Arial,sans-serif;color:var(--text)}
.panel{position:absolute;left:80px;width:1040px;background:var(--white);overflow:hidden}
.panel--home{top:21px;height:639px}
.panel--solutions{top:687px;height:2323px}

/* header */
.site-header{position:absolute;left:0;top:0;width:100%;height:94px;background:var(--white)}
.brand{position:absolute;left:65px;top:34px;font-size:30px;font-weight:700;color:var(--logo);letter-spacing:.5px}
.main-nav{position:absolute;top:46px;left:0;font-size:12px;font-weight:500;color:var(--ink);letter-spacing:.2px}
.main-nav span{position:absolute;white-space:nowrap}
.call{position:absolute;right:63px;top:31px;color:var(--orange)}
.call small{display:block;font-size:11px;font-weight:700;letter-spacing:.3px}
.call strong{display:block;font-size:21px;font-weight:700;margin-top:3px}

/* hero */
.hero{position:absolute;left:0;top:94px;width:100%;height:545px;background:linear-gradient(110deg,#1d2226 0%,#2e3438 40%,#3a3f3c 60%,#1f2a30 100%)}
.hero-title{position:absolute;left:65px;top:162px;font-size:39px;font-weight:900;line-height:38px;color:var(--white);text-transform:uppercase;width:560px}
.hero-text{position:absolute;left:65px;top:250px;width:515px;font-size:19.5px;line-height:33px;color:var(--white)}
.lead-form{position:absolute;left:689px;top:113px;width:286px;height:317px;background:var(--white);border-radius:8px;padding:22px 18px}
.lead-form h2{font-size:22px;font-weight:500;text-align:center;color:var(--ink);line-height:27px;margin-bottom:19px}
.field{height:42px;border:1px solid var(--line);margin-bottom:10px;padding-left:13px;font-size:12px;line-height:40px;color:var(--ink)}
.btn{height:42px;background:var(--orange);color:var(--white);font-weight:700;font-size:15px;text-align:center;line-height:42px;margin-top:2px}
.hero-foot{position:absolute;left:65px;right:63px;top:484px;border-top:1px solid rgba(255,255,255,.3);height:60px}
.hero-foot p{position:absolute;left:0;top:24px;font-size:11px;color:var(--white)}
.social{position:absolute;display:flex;gap:19px}
.social i{display:block;width:18px;height:18px;border-radius:50%;background:var(--white)}
.hero-foot .social{right:20px;top:20px}

/* banner */
.page-banner{position:absolute;left:0;top:94px;width:100%;height:193px;background:linear-gradient(90deg,#23272d,#3c4148 50%,#272b31)}
.page-banner h1{position:absolute;width:100%;top:74px;text-align:center;color:var(--white);font-size:37px;font-weight:900;letter-spacing:.5px}

/* features */
.photo{position:absolute;width:366px;height:302px;background:var(--white);padding:6px;box-shadow:0 0 4px rgba(0,0,0,.3)}
.photo div{width:100%;height:100%}
.feature-text{position:absolute;font-size:12.5px;line-height:20.5px;color:var(--text)}
.feature-text h3{font-size:24px;font-weight:500;color:var(--ink);margin-bottom:8px}
.feature-text ul{list-style:none;margin-top:8px}
.feature-text li{position:relative;padding-left:29px;margin-bottom:7px}
.feature-text li::before{content:"";position:absolute;left:0;top:5px;width:10px;height:10px;border-radius:50%;background:var(--orange)}
.feature-text li::after{content:"";position:absolute;left:3px;top:8px;width:4px;height:2px;border-left:1.5px solid #fff;border-bottom:1.5px solid #fff;transform:rotate(-45deg)}
.left{left:65px}.right-img{left:605px}.right-text{left:455px;width:517px}.left-text{left:65px;width:506px}

/* footer */
.site-footer{position:absolute;left:0;top:2108px;width:100%;height:215px;background:var(--footer);color:var(--footer-text);font-size:12px}
.site-footer .brand{top:50px;color:#777;font-size:30px}
.foot-copy{position:absolute;left:65px;top:95px;line-height:18px;font-size:11px}
.site-footer .social{left:65px;top:143px;gap:19px}
.foot-col{position:absolute;top:40px;line-height:25.5px}
.foot-col h4{font-size:11.5px;font-weight:700;color:var(--white);margin-bottom:2px;letter-spacing:.3px}
.contact-row{position:relative;padding-left:29px}
.contact-row svg{position:absolute;left:0;top:5px}
</style>
</head>
<body>

<section class="panel panel--home">
  <header class="site-header">
    <div class="brand">VENNATRA</div>
    <nav class="main-nav"><span style="left:297px">SOLUTIONS</span><span style="left:406px">HOW WE DO IT</span><span style="left:533px">OUR PEOPLE</span><span style="left:649px">OUR TECHNOLOGY</span></nav>
    <div class="call"><small>CALL US TODAY</small><strong>1-800-555-0148</strong></div>
  </header>
  <div class="hero" role="img" aria-label="Hands holding a tablet over a dark collage of world news pages and maps">
    <h1 class="hero-title">Delivering Global Media Intelligence</h1>
    <p class="hero-text">Vennatra is an international media intelligence service provider. We help communications teams build and operate truly global media monitoring and measurement programmes.</p>
    <form class="lead-form">
      <h2>Learn More About<br>Vennatra</h2>
      <div class="field">Name</div>
      <div class="field">Email Address</div>
      <div class="field">Phone No</div>
      <div class="btn">GET STARTED</div>
    </form>
    <div class="hero-foot">
      <p>Copyright © 2019 Company Name &nbsp;All Rights Reserved</p>
      <div class="social"><i></i><i></i><i></i><i></i><i></i></div>
    </div>
  </div>
</section>

<section class="panel panel--solutions">
  <header class="site-header">
    <div class="brand">VENNATRA</div>
    <nav class="main-nav"><span style="left:297px">SOLUTIONS</span><span style="left:406px">HOW WE DO IT</span><span style="left:533px">OUR PEOPLE</span><span style="left:649px">OUR TECHNOLOGY</span></nav>
    <div class="call"><small>CALL US TODAY</small><strong>1-800-555-0148</strong></div>
  </header>
  <div class="page-banner" role="img" aria-label="Close-up of a hand using a touch screen"><h1>SOLUTIONS</h1></div>

  <figure class="photo left" style="top:338px"><div role="img" aria-label="Hands holding a tablet on a wooden desk" style="background:linear-gradient(135deg,#d9b48a,#b5835a 50%,#6e4a30)"></div></figure>
  <div class="feature-text right-text" style="top:377px">
    <h3>Content Sourcing</h3>
    <p>We help you build a content strategy that meets your budget and coverage needs across earned media - Print, Online, TV and Radio.</p>
    <ul>
      <li>Identify geographies and markets of interest</li>
      <li>Build target media source lists to fulfil monitoring and measurement requirements</li>
      <li>Using our transparent cost calculator, we help you with accurate budgeting and choices to ensure you meet your strategy and objectives</li>
      <li>Translate and localise keyword searches and editorial instructions into effecient source-/ country-/ provider-specific needs to minimise wasted content.</li>
    </ul>
  </div>

  <div class="feature-text left-text" style="top:796px">
    <h3>Content Collection</h3>
    <p>We consolidate and manage the delivery of your global media content into a Cloud-based scalable media platform, taking the headache of content management away from your teams..</p>
  </div>
  <figure class="photo right-img" style="top:690px"><div role="img" aria-label="Businesswoman in front of a blue digital data wall" style="background:linear-gradient(160deg,#6f8fd6,#2f4fa8 55%,#10204f)"></div></figure>

  <figure class="photo left" style="top:1044px"><div role="img" aria-label="Hands holding a phone with a content illustration" style="background:linear-gradient(135deg,#e8dccb,#c7b29a 50%,#8fb7c4)"></div></figure>
  <div class="feature-text right-text" style="top:1044px">
    <h3>Content Augmentation</h3>
    <ul>
      <li>We manage and normalise all of the source-level reference data - country, language, reach etc.</li>
      <li>We add editorial validation to ensure only the content required reaches your delivery, removing inevitable noise from source providers</li>
      <li>Tagging - AI and human based tagging to detect locations, people, topics, products, brands, services, etc.</li>
      <li>Human and automated grouping of stories across geographies - clustering, "also-in" groupings etc.</li>
      <li>Translation summarisation - AI Translation or human-created depending on budget, speed of delivery and need.</li>
      <li>Digest authoring - refining the essence of today’s coverage into a concise board-ready output for your organisation.</li>
    </ul>
  </div>

  <div class="feature-text left-text" style="top:1461px">
    <h3>Content Delivery</h3>
    <p>Early morning delivery of a consolidated, ready-to-consume media coverage</p>
    <ul>
      <li>Customised email templates, delivering content in templates designed to meet your needs</li>
      <li>Customised platform - modern portal tailored to meet your media management needs, removing the unwanted clutter and focusing on the job at hand</li>
      <li>Integration with Intranets, third-party communication tools e.g. Chattro, RSS readers, customised APIs</li>
    </ul>
  </div>
  <figure class="photo right-img" style="top:1407px"><div role="img" aria-label="Woman touching a large interactive news display" style="background:linear-gradient(135deg,#3f6f8f,#1f3a55 55%,#0f1c2c)"></div></figure>

  <figure class="photo left" style="top:1758px"><div role="img" aria-label="Hands holding a tablet showing online news content" style="background:linear-gradient(135deg,#c9d6e6,#5a6f8f 50%,#23324a)"></div></figure>
  <div class="feature-text right-text" style="top:1760px">
    <h3>Media Insights &amp; Consultancy</h3>
    <ul>
      <li>Levering the normalised content sets from your integrated monitoring service, we can analyse and tag your coverage based on complex qualitative measurement criteria, consistent across all languages and geographies, to combine with quantitative metrics.</li>
      <li>Ability to create a single consistent measurement programme across all of your global operations.</li>
      <li>Consultancy to HQ and local offices on how to utilise and align existing measurement and insight intiatives to provide continuity.</li>
      <li>Customised online dashboards with near real time data insights, coupled with Board-ready offline reporting and export options.</li>
      <li>Integration with social media content, third-party data, point-of-sale, web analytics, and delivering on your Integrated Communications Framework</li>
    </ul>
  </div>

  <footer class="site-footer">
    <div class="brand">VENNATRA</div>
    <p class="foot-copy">Copyright © 2019 Company Name<br>All Rights Reserved</p>
    <div class="social"><i></i><i></i><i></i><i></i><i></i></div>
    <div class="foot-col" style="left:297px"><h4>QUICK LINKS</h4>Solutions<br>How we do it<br>Our people<br>Our Technology</div>
    <div class="foot-col" style="left:496px"><h4>SOLUTIONS</h4>Content Sourcing<br>Content Collection<br>Content Augmentation<br>Content Delivery<br>Media Insights &amp; Consultancy</div>
    <div class="foot-col" style="left:766px;line-height:20px"><h4 style="margin-bottom:8px">CONTACT INFO</h4>
      <div>42 Harbourline Street</div><div style="margin-bottom:4px">Linmouth, LM7 2QX</div>
      <div class="contact-row"><svg width="11" height="11" viewBox="0 0 24 24"><path fill="#e6e6e6" d="M6.6 10.8a15 15 0 0 0 6.6 6.6l2.2-2.2c.3-.3.7-.4 1-.2 1.1.4 2.3.6 3.6.6.6 0 1 .4 1 1V20c0 .6-.4 1-1 1A17 17 0 0 1 3 4c0-.6.4-1 1-1h3.5c.6 0 1 .4 1 1 0 1.3.2 2.5.6 3.6.1.3 0 .7-.2 1z"/></svg>1-800-555-0148</div>
      <div class="contact-row"><svg width="12" height="10" viewBox="0 0 24 18"><path fill="#e6e6e6" d="M0 0h24v18H0z"/><path fill="none" stroke="#333" stroke-width="2" d="M1 1l11 9 11-9"/></svg>hello@vennatra-mail.com</div>
    </div>
  </footer>
</section>

</body>
</html>
```